Start my own business with coaching / consulting / hypnosis website (www.marcoveltrup.de) and need

These graphics should represent the process of a coaching / floatpulse / high-performance coaching / hypnosis session, which I conduct with the client. The client should get easier and simpler idea of ​​WHAT exactly happens in such a session and HOW it happens. The customer should always have a positive added value and benefit for him. So the customer leaves the session satisfied and happy and can easily master his initial challenge. The categories I need are: -Coaching -solution finding-entanglements / dependencies -Floatpulse Coaching -high-performance coaching -Hypnosis Session -counselling / couple counseling -Systemic installation Please, 3 to 4 pictures each characterizing the process of the individual categories from beginning to end. Since the beginning and the end of the process, I only need the changing middle part. As a male coach, so please include me in the pictures. --Coaching ----- 3-4 pictures -Clarify the issue -Expand perspectives and options / find the way to a solution for the solution -Finally finding and integrating the right solution -customer is happy and goodbye - -solution-finding --------- 1 picture The only thing that becomes clear is that the solution is read with the client, who usually does not see this solution, or it is not visible to him or the client discovers it means the help of the coach, he can also use it. -Enmeschments / Dependencies ----- 1 Picture picture where clearly people often have entanglements / dependencies on other people / things and thus often in a child of entanglements, which in turn to influence this person. --Floatpulse ----- Middle part: 1 picture -Clarify the issue -Expand perspectives and options / find the way to a solution / set to impulse for the solution -Seat in front of each other and initiate the manual REM phase with the hand of the coach. -customer is Happy and goodbye High Performance Coaching -------- middle section 1-2 pictures -Clarify the issue -Expand perspectives and options / find the way to a solution / set to impulse for the solution -Recognize and awaken potentials in the client ---> superwoman / ironhawk (the gesture where ironhawk tears his shirt is open and underneath his ironhawk sign gets visible on his chest) -customer is happy and goodbye-hypnosis session ----- middle section 1 -2 pictures -Clarify the issue -Expand perspectives and options / find the way to a solution for the solution -both sit relaxed in the armchair -Hypnosis is carried out: Coach speaks to the client, who closes his eyes and imagines the situation in the unconscious. -customer is happy and goodbye --Consulting / Couples consulting / Relationship consulting ----- 3-4 pictures -person / couple comes with concerns, clarifies -expand perspectives and options / find the way to a solution / set impulse for the solution -imparting new knowledge, lovingly talking about it, interaction of the couple, it may also be fun and easy-perspectives -customer / couple is happy and says goodbye - Systemic Constellation- 1-2 Pictures -person / couple comes with concerns, these concerns clarify -other persons are placed in a room and represent persons / family members / personal shares -the solution to the problem itself-to-be-happy

```html
<!DOCTYPE html>
<html lang="en">
<head>
<meta charset="utf-8">
<title>Marco Veltrup – Coaching</title>
<link href="https://fonts.googleapis.com/css2?family=Mulish:wght@400;600;700;800&display=swap" rel="stylesheet">
<style>
:root{
  --ink:#111;
  --text:#222;
  --muted:#555;
  --white:#fff;
  --band:#e6e6e6;
  --quote:#f2f2f2;
  --dark:#242424;
  --footer:#1f1f1f;
}
*{box-sizing:border-box;margin:0;padding:0}
html,body{width:1200px;height:2769px;overflow:hidden}
body{font-family:"Mulish",Arial,sans-serif;color:var(--text);background:var(--white);position:relative}
.abs{position:absolute}

/* hero */
.hero{left:0;top:0;width:1200px;height:615px;background:radial-gradient(circle at 50% 45%,#0e0d0c 0,#2e2a27 18%,#5b544e 45%,#3a3531 75%,#2a2623 100%)}
.brand{left:143px;top:24px;font-size:33px;font-weight:700;color:var(--white)}
.nav{top:40px;right:145px;display:flex;gap:40px;font-size:15px;color:var(--white)}
.nav span.active{text-decoration:underline;text-underline-offset:4px}
.hero-title{left:0;width:1200px;top:268px;text-align:center;font-size:47px;font-weight:400;color:var(--white)}
.hero-btn{left:480px;top:343px;width:240px;height:48px;border:2px solid var(--white);color:var(--white);font-size:19px;display:flex;align-items:center;justify-content:center}
.hero-arrow{top:322px}

/* about */
.h2{font-weight:700;color:var(--ink);font-size:48px}
.about-title{left:145px;top:722px}
.about-text{left:145px;top:794px;width:590px;font-size:12.6px;line-height:25.5px;letter-spacing:-0.1px;color:var(--text)}
.outline-btn{border:2px solid var(--ink);color:var(--ink);display:flex;align-items:center;justify-content:center;font-size:16px}
.about-btn{left:145px;top:990px;width:120px;height:46px}
.portrait{left:755px;top:739px;width:299px;height:299px;border-radius:50%;background:radial-gradient(circle at 50% 35%,#c79c80 0,#a07a64 22%,#eeeeee 52%,#6e6670 75%,#55505a 100%)}

/* services */
.services-band{left:0;top:1117px;width:1200px;height:570px;background:var(--band)}
.services-title{left:0;width:1200px;top:1182px;text-align:center}
.card{top:1265px;width:212px;height:160px;background:var(--white);display:flex;flex-direction:column;align-items:center;padding-top:24px;font-size:16px;font-weight:600;color:var(--ink)}
.card svg{margin-bottom:18px}
.card.active{background:var(--dark);color:var(--white)}
.how{left:145px;top:1428px;width:910px;height:339px;background:var(--dark)}
.pointer{left:233px;top:1425px}
.how-title{left:145px;width:910px;top:1472px;text-align:center;color:var(--white);font-size:24px;font-weight:400}
.step{top:1522px;width:160px;height:160px;border-radius:50%;background:radial-gradient(circle at 45% 50%,#cfe9ef 0,#f5f5f5 55%,#ffffff 100%)}
.step-label{top:1690px;width:190px;text-align:center;color:var(--white);font-size:11.5px;line-height:18px}
.connector{top:1601px;height:2px;width:54px;background:var(--white)}

/* testimonials */
.testi-title{left:0;width:1200px;top:1752px;text-align:center}
.quote{top:1833px;width:443px;height:142px;background:var(--quote);padding:22px 22px;font-size:14px;line-height:25px;color:var(--muted);text-align:center}
.quote::after{content:"";position:absolute;left:206px;bottom:-15px;border-left:15px solid transparent;border-right:15px solid transparent;border-top:15px solid var(--quote)}
.avatar{top:2004px;width:54px;height:54px;border-radius:50%;background:radial-gradient(circle at 50% 40%,#b59a8a 0,#8a7568 50%,#c9c3bd 100%)}
.person{top:2066px;width:200px;text-align:center;font-size:16px;color:var(--ink)}
.stars{top:2090px;width:200px;text-align:center;font-size:12px;letter-spacing:2px;color:var(--ink)}

/* contact */
.contact-band{left:0;top:2184px;width:1200px;height:487px;background:var(--band)}
.contact-title{left:0;width:1200px;top:2249px;text-align:center}
.field{top:2341px;width:218px;height:39px;background:var(--white);border:1px solid #bbb;font-size:11.5px;color:#666;padding:12px 14px}
.message{left:145px;top:2402px;width:910px;height:126px;background:var(--white);border:1px solid #bbb;font-size:11.5px;color:#666;padding:14px 4px}
.submit{left:548px;top:2549px;width:103px;height:44px;font-size:15px;background:transparent}

/* footer */
.footer{left:0;top:2671px;width:1200px;height:98px;background:var(--footer)}
.foot-links{left:143px;top:2697px;font-size:11px;color:#cfcfcf}
.copyright{left:143px;top:2727px;font-size:11px;color:#cfcfcf}
.social{top:2703px;width:32px;height:32px;border-radius:50%;background:#6d6d6d}
</style>
</head>
<body>

<section class="abs hero" role="img" aria-label="Photograph looking down a spiral stone staircase"></section>
<div class="abs brand">Marco Veltrup</div>
<nav class="abs nav"><span class="active">Home</span><span>About Me</span><span>Services</span><span>Testimonials</span><span>Contact Me</span></nav>
<h1 class="abs hero-title">Proin placerat dapibus gravida</h1>
<div class="abs hero-btn">Book an Appointment</div>
<svg class="abs hero-arrow" style="left:46px" width="22" height="36" viewBox="0 0 22 36"><path d="M18 4 L5 18 L18 32" fill="none" stroke="#fff" stroke-width="4"/></svg>
<svg class="abs hero-arrow" style="left:1132px" width="22" height="36" viewBox="0 0 22 36"><path d="M4 4 L17 18 L4 32" fill="none" stroke="#fff" stroke-width="4"/></svg>

<h2 class="abs h2 about-title">About Me</h2>
<p class="abs about-text">Maecenas vel tortor accumsan quam varius imperdiet vel eget elit. Aenean facilisis tincidunt lectus, id dictum nisi luctus eget. Vivamus efficitur ex condimentum, malesuada eros eget, feugiat nibh. Sed tellus ex, imperdiet eget gravida sit amet, volutpat eget turpis. In nec ultricies est. Etiam mattis augue vehicula odio posuere, sit amet tempus lectus luctus. Nulla facilisi. Etiam vel massa elementum, bibendum tellus venenatis, feugiat massa. Curabitur venenatis lacinia ornare. Cras sollicitudin cursus dui eu placerat. Pellentesque a imperdiet dolor, et auctor est. Fusce sollicitudin lorem et luctus volutpat. Proin placerat dapibus gravida.</p>
<div class="abs outline-btn about-btn">Contact Me</div>
<div class="abs portrait" role="img" aria-label="Portrait photo of the coach in a white shirt"></div>

<div class="abs services-band"></div>
<h2 class="abs h2 services-title">Services</h2>
<div class="abs card active" style="left:145px">
  <svg width="60" height="56" viewBox="0 0 60 56" fill="none" stroke="#fff" stroke-width="2"><rect x="20" y="2" width="22" height="14"/><circle cx="18" cy="30" r="6"/><circle cx="42" cy="30" r="6"/><path d="M6 54v-8a12 10 0 0 1 24 0v8M30 54v-8a12 10 0 0 1 24 0v8"/></svg>
  Coaching
</div>
<div class="abs card" style="left:378px">
  <svg width="60" height="56" viewBox="0 0 60 56" fill="none" stroke="#111" stroke-width="2"><rect x="8" y="4" width="20" height="20"/><rect x="30" y="12" width="20" height="20"/><rect x="12" y="28" width="20" height="20"/><rect x="34" y="34" width="18" height="18"/></svg>
  Solution Finding
</div>
<div class="abs card" style="left:611px">
  <svg width="60" height="56" viewBox="0 0 60 56" fill="none" stroke="#111" stroke-width="2"><circle cx="30" cy="28" r="24"/><circle cx="30" cy="28" r="15"/><circle cx="30" cy="28" r="6"/><path d="M30 4v8M30 44v8M6 28h8M46 28h8"/></svg>
  Entanglements
</div>
<div class="abs card" style="left:844px">
  <svg width="60" height="56" viewBox="0 0 60 56" fill="none" stroke="#111" stroke-width="2"><path d="M4 54h52"/><rect x="8" y="40" width="7" height="12"/><rect x="19" y="32" width="7" height="20"/><rect x="30" y="26" width="7" height="26"/><rect x="41" y="18" width="7" height="34"/><path d="M8 30 L22 20 L32 22 L50 6M42 6h8v8"/></svg>
  Floatpulse Coaching
</div>

<div class="abs how"></div>
<svg class="abs pointer" width="32" height="16" viewBox="0 0 32 16"><path d="M0 0 H32 V3 H0 Z" fill="#e6e6e6"/><path d="M1 0 L16 14 L31 0 Z" fill="#242424"/><path d="M1 3 L16 14 L31 3" fill="none" stroke="#fff" stroke-width="1.5"/></svg>
<h3 class="abs how-title">HOW IT WORKS</h3>
<div class="abs step" style="left:169px" role="img" aria-label="Illustration of a head in profile with question marks"></div>
<div class="abs step" style="left:402px" role="img" aria-label="Illustration of a head in profile with expanding circles and options"></div>
<div class="abs step" style="left:636px" role="img" aria-label="Illustration of a head in profile with a target and arrow"></div>
<div class="abs step" style="left:871px" role="img" aria-label="Illustration of a head in profile with a growing tree"></div>
<div class="abs connector" style="left:337px"></div>
<div class="abs connector" style="left:571px"></div>
<div class="abs connector" style="left:806px"></div>
<div class="abs step-label" style="left:154px">Clarify the issue</div>
<div class="abs step-label" style="left:387px">Expand perspectives and<br>options</div>
<div class="abs step-label" style="left:621px">Finally finding and integrating<br>the right solution</div>
<div class="abs step-label" style="left:856px">Customer is Happy and<br>goodbye</div>

<h2 class="abs h2 testi-title">Testimonials</h2>
<svg class="abs" style="left:56px;top:1891px" width="14" height="24" viewBox="0 0 14 24"><path d="M12 2 L3 12 L12 22" fill="none" stroke="#999" stroke-width="2"/></svg>
<svg class="abs" style="left:1130px;top:1891px" width="14" height="24" viewBox="0 0 14 24"><path d="M2 2 L11 12 L2 22" fill="none" stroke="#999" stroke-width="2"/></svg>
<div class="abs quote" style="left:145px">" Fusce vitae lectus sit amet mi pulvinar maximus. Aenean placerat, nibh vel accumsan aliquet, magna nibh accumsan nibh, ac tempus nunc ipsum ac tellus. Cras augue magna, placerat eget nulla. "</div>
<div class="abs quote" style="left:611px">" Aliquam erat volutpat. Quisque aliquet ex nec est vestibulum pulvinar. Pellentesque convallis molestie enim sit amet efficitur. Etiam id imperdiet lectus. Vivamus lacus justo, ultrices nec erat in, euismod iaculis mauris. "</div>
<div class="abs avatar" style="left:339px" role="img" aria-label="Client portrait photo"></div>
<div class="abs avatar" style="left:806px" role="img" aria-label="Client portrait photo"></div>
<div class="abs person" style="left:266px">Tom Harlan</div>
<div class="abs person" style="left:733px">Lena Moor</div>
<div class="abs stars" style="left:266px">★★★★★</div>
<div class="abs stars" style="left:733px">★★★★★</div>

<div class="abs contact-band"></div>
<h2 class="abs h2 contact-title">Contact Us</h2>
<div class="abs field" style="left:145px">Name</div>
<div class="abs field" style="left:376px">Email</div>
<div class="abs field" style="left:606px">Phone</div>
<div class="abs field" style="left:837px">Service for
  <svg class="abs" style="right:14px;top:16px" width="10" height="6" viewBox="0 0 10 6"><path d="M0 0h10L5 6z" fill="#333"/></svg>
</div>
<div class="abs message">Message</div>
<div class="abs outline-btn submit">SUBMIT</div>

<footer class="abs footer"></footer>
<div class="abs foot-links">Home &nbsp;|&nbsp; About Me &nbsp;|&nbsp; Services &nbsp;|&nbsp; Testimonials &nbsp;|&nbsp; Contact Me</div>
<div class="abs copyright">Copyright © 2018 &nbsp;Marco Veltrup. &nbsp;All rights reserved.</div>
<div class="abs social" style="left:977px"></div>
<div class="abs social" style="left:1021px"></div>

</body>
</html>
```